Are You Frackin Ready?

Purpose - Come up with an ad design that promotes the "Turbo Arbor featuring Merged Profiler" product. The ad should direct readers to visit www.brovantco.com/tmp.htm or call Brovant Tooling Inc Dallas Houston Tulsa (800) 472-9038 for more information.

Ad size
Full Page w/Bleed
11.125” W by 14.125” D

Full Page Trim
10.875” W by 13.875” D

Notes to To Designer - This particular product will be widely used on machining centers to process parts used in the oil and gas industry like fluid ends used in the fracking process that require a significant amount of time to machine. It will give greatly improve productivity and accuracy. The fracking process is a massive industry and growing worldwide each and every day so there are opportunities for each and every oil and gas related component manufacturer or processor to capitalize on the manufacturing and machining of components.

Useful Phrases and Headers I would like to use -

"ARE YOU FRACKIN READY"

"Two Heads Really Are Better Than One"

Ad Copy - Available on 800mm to 1600mm horizontal spindle platforms, the a Turbo Arbor featuring Merged Profiler Head optimizes spindle utilization, part quality and productivity of complex components by greatly reducing setups, head changes, and part handling.
Updates

lets get rid of the "Are You Frackin Ready" and replace it with "TWO HEADS REALLY ARE BETTER THAN ONE" because i am getting too much negative feedback from people i have reviewing the ad

Industry/Entity Type

Oil And Gas

```html
<!DOCTYPE html>
<html lang="en">
<head>
<meta charset="utf-8">
<title>Two Heads Really Are Better Than One — Brovant Tooling Inc</title>
<link rel="stylesheet" href="https://fonts.googleapis.com/css2?family=Montserrat:wght@300;400;600;700;800&family=Roboto+Condensed:wght@700&family=Arimo:wght@400&display=swap">
<style>
  :root {
    --orange: #d9622b;
    --ink: #1a1a1a;
    --white: #ffffff;
    --yellow-light: #fff6d6;
    --yellow-mid: #ffd85a;
    --yellow-deep: #fcc21c;
    --wave-orange: #f07f1e;
    --wave-yellow: #ffd23a;
    --green: #0f7a3c;
    --green-dark: #0b5e2d;
    --green-text: #2a9a3c;
    --steel: #b9bcbf;
    --photo-light: #e4e6e8;
    --photo-dark: #3a3c3e;
  }
  * { margin: 0; padding: 0; box-sizing: border-box; }
  html, body { width: 945px; height: 1200px; overflow: hidden; background: var(--white); }
  .ad { position: relative; width: 945px; height: 1200px; overflow: hidden; background: var(--white); font-family: "Montserrat", sans-serif; color: var(--ink); }

  .headline { position: absolute; top: 70px; left: 0; width: 945px; text-align: center; }
  .headline-main { font-weight: 800; font-size: 86px; line-height: 1; color: var(--orange); letter-spacing: 1px; }
  .headline-sub { margin-top: 8px; font-weight: 300; font-size: 37px; line-height: 1; letter-spacing: 0.5px; }
  .headline-sub strong { font-weight: 700; }

  .machine-photo { position: absolute; top: 250px; left: 0; width: 945px; height: 520px;
    background: linear-gradient(90deg, var(--photo-dark) 0%, #7d8083 12%, var(--photo-light) 30%, #f2f2f2 55%, #8c8e90 72%, #5b5d60 85%, var(--photo-light) 100%); }

  .yellow-field { position: absolute; top: 0; left: 0; width: 945px; height: 1200px; }

  .pitch { position: absolute; left: 77px; top: 828px; width: 590px; }
  .pitch-title { font-weight: 600; font-size: 26.5px; line-height: 1.25; letter-spacing: 0.3px; }
  .pitch-body { margin-top: 4px; font-weight: 400; font-size: 17.5px; line-height: 1.3; }
  .pitch-body strong { font-weight: 700; }

  .contact { position: absolute; left: 77px; top: 1093px; }
  .contact-web { font-family: "Arimo", sans-serif; font-size: 24px; line-height: 1.3; }
  .contact-call { font-family: "Roboto Condensed", sans-serif; font-weight: 700; font-size: 25px; line-height: 1.3; }
  .contact .accent { color: var(--green-text); }

  .brand-band { position: absolute; left: 680px; top: 880px; width: 210px; height: 320px;
    background: linear-gradient(180deg, var(--green) 0%, var(--green-dark) 100%); }
  .brand-disc { position: absolute; left: 668px; top: 712px; width: 220px; height: 220px; border-radius: 50%;
    background: radial-gradient(circle at 40% 35%, #eef0f1 0%, var(--steel) 60%, #7e8285 100%); }
  .brand-name { position: absolute; left: 680px; top: 960px; width: 210px; text-align: center;
    font-weight: 700; font-size: 20px; line-height: 1.25; color: var(--white); letter-spacing: 0.5px; }
  .brand-url { position: absolute; left: 680px; top: 1134px; width: 210px; text-align: center;
    font-family: "Arimo", sans-serif; font-size: 17px; color: var(--white); }
</style>
</head>
<body>
<main class="ad">
  <header class="headline">
    <h1 class="headline-main">TWO HEADS</h1>
    <p class="headline-sub">REALLY ARE <strong>BETTER THAN ONE</strong></p>
  </header>

  <div class="machine-photo" role="img" aria-label="Photograph of a horizontal machining center with a black cable-carrier arm reaching to a steel head block carrying a contouring facing head"></div>

  <svg class="yellow-field" width="945" height="1200" viewBox="0 0 945 1200" aria-hidden="true">
    <defs>
      <linearGradient id="fieldFill" x1="0" y1="0" x2="0" y2="1">
        <stop offset="0" stop-color="var(--yellow-light)"/>
        <stop offset="0.35" stop-color="#ffeaa0"/>
        <stop offset="0.7" stop-color="var(--yellow-mid)"/>
        <stop offset="1" stop-color="var(--yellow-deep)"/>
      </linearGradient>
    </defs>
    <path d="M0 650 C 180 640 300 700 470 730 C 620 755 760 760 945 800 L945 1200 L0 1200 Z" fill="url(#fieldFill)"/>
    <path d="M0 626 C 160 650 330 700 480 712 C 620 722 720 700 945 770" fill="none" stroke="var(--wave-yellow)" stroke-width="5"/>
    <path d="M0 668 C 170 660 320 690 470 720 C 620 750 760 765 945 770" fill="none" stroke="var(--wave-orange)" stroke-width="6"/>
    <path d="M0 690 C 200 676 360 720 500 740 C 660 764 780 800 945 812" fill="none" stroke="var(--wave-yellow)" stroke-width="4"/>
    <path d="M0 705 C 220 690 380 730 540 760 C 700 790 820 830 945 840" fill="none" stroke="var(--wave-orange)" stroke-width="3" opacity="0.8"/>
  </svg>

  <section class="pitch">
    <h2 class="pitch-title">AVAILABLE ON 800MM TO 1600MM HORIZONTAL SPINDLE PLATFORMS.</h2>
    <p class="pitch-body">A <strong>Turbo Arbor</strong> featuring Merged Profiler Head optimizes spindle utilization, part quality and productivity of complex components by greatly reducing setups, head changes, and part handling.</p>
  </section>

  <footer class="contact">
    <p class="contact-web">For more information, visit <span class="accent">www.brovantco.com/tmp.htm</span></p>
    <p class="contact-call">or call Brovant Tooling Inc. at <span class="accent">(800) 472-9038</span></p>
  </footer>

  <div class="brand-band"></div>
  <div class="brand-disc" aria-hidden="true"></div>
  <p class="brand-name">BROVANT<br>TOOLING INC</p>
  <p class="brand-url">www.brovantco.com</p>
</main>
</body>
</html>
```